Mandala Postcard Design

I am in need of a postcard to hand out at a Psychic Fair. I envision the card to having half-of-a Mandala (from my Facebook folder), touched up a bit to make it vibrant and bold. Others vendors will have cards w/photographic backgrounds doing yoga. I'd like mine to stand out for it's line-drawn "cartoonish" nature, solid-color nature. The wording would be my basic contact info and a short description ... something like: "Experience the Magic of Mandala Making ... Next Class will be held: (open space for writing, no lines) The art is contained in this Facebook folder. Lots to choose from, with my favorites being the stronger outlined designs.

https://www.examplesocial.net/Brightorbs/media_set?set=a.20462926615637197.2184852941.783542196&type=3
Updates

I just uploaded a few new drawings that might work better, since they are more round. I want to minimize the white space, for instance, avoid having the left & right corners empty. Another idea could be to use 1/4 mandalas in the corners. I'm ready to make a decision. I want it to look great, but as I gain drawing experience, I'll need to update my cards. Thanks! I'm not sure if this the place for this comment, but I'll also be needing a DVD label for my tutorials, and a front page design for a mandala coloring book.

Target Market(s)

Primarily women interested in metaphysical, psychic, meditation, reiki and a basic interest in art.

Font styles to use
Serif
Sans Serif

Requirements
Should not have
• Should not be on a dark card, really should be a plain white background, it seems, in order to stand out.

```html
<!DOCTYPE html>
<html lang="en">
<head>
<meta charset="utf-8">
<title>Mandala Making Postcard</title>
<link rel="stylesheet" href="https://fonts.googleapis.com/css2?family=Sacramento&family=Arimo:wght@400&display=swap">
<style>
  :root {
    --card-white: #f7f7f5;
    --ink: #2b2b2b;
    --pink: #f3a3c4;
    --yellow: #f5eb8c;
    --cyan: #6ec7e8;
    --red: #d8283c;
    --lilac: #c9b2dc;
  }
  html, body {
    margin: 0;
    padding: 0;
    width: 1200px;
    height: 800px;
    overflow: hidden;
    background: var(--card-white);
  }
  .postcard {
    position: relative;
    width: 1200px;
    height: 800px;
    overflow: hidden;
    background: var(--card-white);
  }
  .mandala-art {
    position: absolute;
    border-radius: 50%;
  }
  .mandala-art--corner-top-left {
    left: -40px; top: -40px;
    width: 250px; height: 250px;
    background: radial-gradient(circle, var(--yellow) 0%, var(--pink) 45%, var(--cyan) 75%, rgba(247,247,245,0) 72%);
  }
  .mandala-art--feature {
    left: 40px; top: 140px;
    width: 530px; height: 450px;
    background: radial-gradient(ellipse at center, var(--red) 0%, var(--yellow) 18%, var(--pink) 40%, var(--cyan) 62%, var(--yellow) 72%, rgba(247,247,245,0) 71%);
  }
  .mandala-art--corner-bottom-left {
    left: -90px; bottom: -90px;
    width: 330px; height: 330px;
    background: radial-gradient(circle, var(--cyan) 0%, var(--lilac) 35%, var(--yellow) 55%, var(--pink) 66%, rgba(247,247,245,0) 70%);
  }
  .mandala-art--quarter-top-right {
    right: -310px; top: -320px;
    width: 640px; height: 590px;
    background: radial-gradient(circle, var(--pink) 0%, var(--yellow) 30%, var(--cyan) 50%, var(--red) 60%, var(--cyan) 66%, rgba(247,247,245,0) 70%);
  }
  .mandala-art--quarter-bottom-right {
    right: -220px; bottom: -330px;
    width: 900px; height: 660px;
    background: radial-gradient(ellipse at center, var(--pink) 0%, var(--yellow) 25%, var(--cyan) 45%, var(--pink) 58%, rgba(247,247,245,0) 70%);
  }
  .invitation {
    position: absolute;
    left: 560px;
    top: 255px;
    width: 560px;
    text-align: center;
    color: var(--ink);
  }
  .invitation__title {
    margin: 0;
    font-family: "Sacramento", cursive;
    font-weight: 400;
    font-size: 64px;
    line-height: 66px;
  }
  .invitation__next-class {
    margin: 30px 0 0 70px;
    text-align: left;
    font-family: "Arimo", sans-serif;
    font-size: 17px;
    letter-spacing: 0.3px;
  }
</style>
</head>
<body>
  <main class="postcard">
    <div class="mandala-art mandala-art--corner-top-left" role="img" aria-label="Colourful quarter mandala ornament in the top left corner"></div>
    <div class="mandala-art mandala-art--feature" role="img" aria-label="Large hand-drawn mandala in pink, yellow, cyan and red with red petal accents"></div>
    <div class="mandala-art mandala-art--corner-bottom-left" role="img" aria-label="Colourful quarter mandala ornament in the bottom left corner"></div>
    <div class="mandala-art mandala-art--quarter-top-right" role="img" aria-label="Half mandala with spiked cyan ring in the top right corner"></div>
    <div class="mandala-art mandala-art--quarter-bottom-right" role="img" aria-label="Partial mandala with pink and cyan petals along the bottom right edge"></div>

    <section class="invitation">
      <h1 class="invitation__title">Experience the Magic of<br>Mandala Making</h1>
      <p class="invitation__next-class">Next Class will be held :</p>
    </section>
  </main>
</body>
</html>
```